Social media agency for startUps! Need captivating web banner(s) needed

We need a few banners if Possible for a lead generation - branding campaign we are about to launch on Workvine & Chatterloop. We are Social media Agency created to help Startup and small medium business build there digital footprint. We also offer a brand analysing service to help brands understand there real time impact along with consulting, coaching and managed services. We are very open to the design concept. We are looking for creativity and professionalism. Something that will captivate and peek interest in learning more about how a company can work with us. We are need banners for Chatterloop and Workvine. If you require the formats please ask and we will send them. 2 for each platform would be nice, but depending on cost we would be happy with i for each network.

Designs should have our tag line : Accelerated Marketing. Refreshing Results. it should alsl speak to the fact that we are the Social Media Agency for Startups in Canada.

Target Market(s)

Small Medium Business and Start up companies

Industry/Entity Type

Media

Requirements
Must have
• company name - TrailMOSS Social
• out tag line - Accelerated Marketing. Refreshing Results
• our Logo -
• ad size -
• 160x600 Workvine
• 30x250 Workvine
• 1,200 x 628 pixels Chatterloop
• Recommended image size: 600 x 600 pixels
Nice to have
• This is the hard part - I would like to see something like a collage of all the social networks and how our brand connects them to the business in question. The other aspect could be something related to when you leveled up in a video game.
• i know this is somewhat vague, but i am open to any question you might have relating to this project.

```html
<!DOCTYPE html>
<html lang="en">
<head>
<meta charset="utf-8">
<title>TrailMOSS Social – Accelerated Marketing</title>
<link href="https://fonts.googleapis.com/css2?family=Oswald:wght@300;400;500&family=Roboto:wght@400&display=swap" rel="stylesheet">
<style>
  :root {
    --navy: #23242f;
    --navy-deep: #1c1d26;
    --orange: #f7931e;
    --white: #ffffff;
    --grey-text: #a7a9b4;
    --photo-light: #eef0f2;
    --photo-mid: #c9d2d8;
    --photo-teal: #7fa9a6;
    --arrow-warm: #8a3a2a;
  }
  * { margin: 0; padding: 0; box-sizing: border-box; }
  html, body {
    width: 1200px;
    height: 1200px;
    overflow: hidden;
    background: var(--navy);
  }
  .banner {
    position: relative;
    width: 1200px;
    height: 1200px;
    background: var(--navy);
    overflow: hidden;
    font-family: "Oswald", sans-serif;
  }
  .growth-glow {
    position: absolute;
    left: 620px;
    top: 30px;
    width: 320px;
    height: 560px;
    background: linear-gradient(180deg, rgba(138,58,42,0.55) 0%, rgba(120,70,40,0.25) 60%, rgba(35,36,47,0) 100%);
    filter: blur(6px);
  }
  .feature-visual {
    position: absolute;
    inset: 0;
  }
  .brand {
    position: absolute;
    left: 60px;
    top: 150px;
  }
  .brand-name {
    display: flex;
    align-items: center;
    gap: 18px;
    font-weight: 400;
    font-size: 46px;
    letter-spacing: 3px;
    text-transform: uppercase;
    color: var(--white);
    line-height: 1;
  }
  .brand-mark {
    width: 38px;
    height: 38px;
    background: var(--orange);
  }
  .brand-tagline {
    margin-top: 14px;
    font-family: "Roboto", sans-serif;
    font-size: 21px;
    color: var(--white);
    letter-spacing: 0.5px;
  }
  .services {
    position: absolute;
    left: 56px;
    top: 376px;
    list-style: none;
  }
  .services li {
    position: relative;
    padding-left: 44px;
    height: 87px;
    font-weight: 400;
    font-size: 44px;
    letter-spacing: 1px;
    color: var(--grey-text);
    text-transform: uppercase;
    line-height: 60px;
  }
  .services li::before {
    content: "";
    position: absolute;
    left: 4px;
    top: 27px;
    width: 9px;
    height: 9px;
    border-radius: 50%;
    background: var(--grey-text);
  }
  .closing-line {
    position: absolute;
    left: 50px;
    top: 920px;
    font-weight: 500;
    font-size: 66px;
    line-height: 88px;
    text-transform: uppercase;
  }
  .closing-line .accent { color: var(--orange); display: block; }
  .closing-line .plain { color: var(--white); display: block; }
</style>
</head>
<body>
  <main class="banner">
    <div class="growth-glow" role="img" aria-label="Faded upward growth arrows rising behind the collage"></div>

    <svg class="feature-visual" width="1200" height="1200" viewBox="0 0 1200 1200">
      <defs>
        <linearGradient id="collageTone" x1="0" y1="0" x2="1" y2="1">
          <stop offset="0" stop-color="var(--photo-mid)"/>
          <stop offset="0.45" stop-color="var(--photo-light)"/>
          <stop offset="0.75" stop-color="var(--photo-teal)" stop-opacity="0.55"/>
          <stop offset="1" stop-color="var(--photo-mid)"/>
        </linearGradient>
      </defs>
      <polygon points="1096,0 1200,0 1200,150 1096,0" fill="var(--navy)"/>
      <polygon role="img" aria-label="Desk photo of a person holding a tablet, overlaid with a marketing word cloud: strategy, advertising, sales, publicity, direct marketing, branding, marketing, public relations, pricing"
        points="1096,0 530,870 776,870 776,1200 1200,1200 1200,150"
        fill="url(#collageTone)"/>
      <polyline points="776,1200 776,870 530,870 1096,0 1200,150"
        fill="none" stroke="var(--orange)" stroke-width="9" stroke-linejoin="miter"/>
    </svg>

    <header class="brand">
      <div class="brand-name"><span class="brand-mark"></span>TrailMOSS Social</div>
      <p class="brand-tagline">Accelerated Marketing. Refreshing results</p>
    </header>

    <ul class="services">
      <li>Brand Analysing Service</li>
      <li>Consulting</li>
      <li>Coaching &amp; Managed Services</li>
      <li>Online Marketing</li>
      <li>Social Media</li>
    </ul>

    <h1 class="closing-line">
      <span class="accent">Accelerated Marketing.</span>
      <span class="plain">Refreshing Results</span>
    </h1>
  </main>
</body>
</html>
```